Heron Loan Partners Business Card

We need a business card design for our mortgage servicing company. In addition to servicing the loans of homeowners, we help homeowners with purchasing their homes and any mortgage refinancing. We would like to see designs that use the colors in the logo attached below (gold-ish yellow and navy blue), and any other design you deem fit! The design should communicate a simpler life with smart mortgages provided by Heron.

```html
<!DOCTYPE html>
<html lang="en">
<head>
<meta charset="UTF-8">
<title>Heron Loan Partners — Business Card</title>
<link href="https://fonts.googleapis.com/css2?family=Libre+Baskerville:wght@700&family=Poppins:wght@400&display=swap" rel="stylesheet">
<style>
  :root {
    --backdrop: #1f1f22;
    --navy: #211d5e;
    --navy-front: #2a2458;
    --gold: #e0b33e;
    --white: #ffffff;
  }
  * { margin: 0; padding: 0; box-sizing: border-box; }
  html, body { width: 1200px; height: 1015px; overflow: hidden; }
  body {
    background: var(--backdrop);
    font-family: "Poppins", sans-serif;
    position: relative;
  }
  .card {
    position: absolute;
    left: 190px;
    width: 820px;
    height: 460px;
    overflow: hidden;
    box-shadow: 0 10px 30px rgba(0,0,0,.5);
  }
  .card-front { top: 30px; background: var(--navy-front); }
  .card-back { top: 525px; background: var(--navy); }

  .brand {
    font-family: "Libre Baskerville", serif;
    font-weight: 700;
    color: var(--gold);
    display: flex;
    align-items: center;
    gap: 16px;
    white-space: nowrap;
  }
  .brand-dot {
    width: 18px; height: 18px;
    border-radius: 50%;
    background: var(--gold);
    flex: none;
  }
  .card-front .brand {
    position: absolute;
    left: 50%; top: 50%;
    transform: translate(-50%, -50%);
    font-size: 48px;
  }

  .gold-panel { position: absolute; inset: 0; }

  .card-back .brand {
    position: absolute;
    left: 712px;
    top: 230px;
    transform: translate(-50%, -50%) rotate(-90deg);
    font-size: 30px;
    gap: 12px;
    color: var(--navy);
  }
  .card-back .brand-dot { background: var(--navy); width: 14px; height: 14px; }

  .contact-block {
    position: absolute;
    left: 60px;
    top: 70px;
    color: var(--white);
  }
  .person-name {
    font-family: "Libre Baskerville", serif;
    font-weight: 700;
    font-size: 32px;
    color: var(--gold);
    line-height: 1.1;
  }
  .person-title { font-size: 21px; line-height: 1.3; margin-bottom: 40px; }
  .contact-list { list-style: none; margin-bottom: 40px; }
  .contact-list li {
    display: flex; align-items: center; gap: 12px;
    font-size: 21px; line-height: 1.45;
  }
  .contact-list svg { width: 20px; height: 20px; flex: none; }
  .address { font-size: 21px; line-height: 1.35; }
</style>
</head>
<body>

<section class="card card-front" aria-label="Card front">
  <div class="brand"><span class="brand-dot"></span>Heron Loan Partners</div>
</section>

<section class="card card-back" aria-label="Card back">
  <svg class="gold-panel" viewBox="0 0 820 460" preserveAspectRatio="none" aria-hidden="true">
    <path d="M560 0 C 600 70, 640 120, 600 200 C 570 270, 600 360, 585 460 L 820 460 L 820 0 Z" fill="var(--gold)"/>
    <path d="M560 0 C 600 70, 640 120, 600 200 C 570 270, 600 360, 585 460" fill="none" stroke="var(--white)" stroke-width="2"/>
  </svg>

  <div class="brand"><span class="brand-dot"></span>Heron Loan Partners</div>

  <div class="contact-block">
    <h1 class="person-name">Daniel Reyes</h1>
    <p class="person-title">Managing Director</p>
    <ul class="contact-list">
      <li>
        <svg viewBox="0 0 24 24" aria-hidden="true"><path fill="var(--gold)" d="M6.6 10.8a15 15 0 0 0 6.6 6.6l2.2-2.2a1 1 0 0 1 1-.25 11.4 11.4 0 0 0 3.6.57 1 1 0 0 1 1 1V20a1 1 0 0 1-1 1A17 17 0 0 1 3 4a1 1 0 0 1 1-1h3.5a1 1 0 0 1 1 1c0 1.250.2 2.450.57 3.57a1 1 0 0 1-.25 1z"/></svg>
        044-987 654 321
      </li>
      <li>
        <svg viewBox="0 0 24 24" aria-hidden="true"><path fill="var(--gold)" d="M2 5h20v14H2z"/><path fill="none" stroke="var(--navy)" stroke-width="1.6" d="M2 5l10 8 10-8"/></svg>
        hello@heronloans.com
      </li>
      <li>
        <svg viewBox="0 0 24 24" aria-hidden="true"><circle cx="12" cy="12" r="10" fill="none" stroke="var(--gold)" stroke-width="2"/><path fill="none" stroke="var(--gold)" stroke-width="1.6" d="M2 12h20M12 2c3 3 3 17 0 20M12 2c-3 3-3 17 0 20"/></svg>
        www.heronloans.com
      </li>
    </ul>
    <p class="address">88, Harbor View Road<br>20417, Country Name</p>
  </div>
</section>

</body>
</html>
```